New Business Card Design Project

We would like a business card that represents the sale of boat, home, auto, and life insurance.

The logo can change colors to meet the look of the design if needed.

Industry/Entity Type

Business

```html
<!DOCTYPE html>
<html lang="en">
<head>
<meta charset="utf-8">
<title>Alder Financial – Business Card</title>
<link href="https://fonts.googleapis.com/css2?family=Open+Sans:wght@400;600&display=swap" rel="stylesheet">
<style>
  :root {
    --backdrop: #d9dcde;
    --paper: #ffffff;
    --teal: #3b6f87;
    --strip: #3a3a3a;
    --ink: #3d3d3d;
    --on-teal: #ffffff;
  }
  * { margin: 0; padding: 0; box-sizing: border-box; }
  html, body {
    width: 1200px; height: 676px; overflow: hidden;
    background: var(--backdrop);
    font-family: "Open Sans", Arial, sans-serif;
  }
  .canvas {
    position: relative; width: 1200px; height: 676px;
    display: flex; align-items: center; justify-content: center; gap: 40px;
  }
  .card {
    position: relative; width: 530px; height: 303px;
    background: var(--paper); overflow: hidden;
    box-shadow: 0 10px 26px rgba(0,0,0,.22);
  }
  .brand {
    display: flex; align-items: center; gap: 8px;
    color: var(--ink); font-weight: 600; letter-spacing: 2px;
    font-size: 22px; text-transform: uppercase; white-space: nowrap;
  }
  .brand__dot {
    flex: none; width: 14px; height: 14px; border-radius: 50%; background: var(--teal);
  }

  /* Front */
  .front .brand { position: absolute; left: 26px; top: 52px; }
  .front__band {
    position: absolute; left: 0; right: 0; bottom: 0; height: 128px;
    background: var(--teal);
  }
  .front__title {
    position: absolute; right: 30px; bottom: 30px;
    color: var(--on-teal); font-size: 16px; letter-spacing: .3px;
  }
  .front__title .role { font-size: 14px; }

  /* Back */
  .back__brandzone {
    position: absolute; left: 0; top: 0; width: 205px; height: 100%;
    display: flex; align-items: center; justify-content: center;
    padding: 0 18px;
  }
  .back .brand { font-size: 15px; letter-spacing: 1px; gap: 7px; }
  .back .brand__dot { width: 11px; height: 11px; }
  .back__panel {
    position: absolute; left: 205px; top: 0; right: 0; bottom: 0;
    background: var(--teal); color: var(--on-teal);
  }
  .back__name { position: absolute; left: 50px; top: 50px; font-size: 19px; }
  .back__role { position: absolute; left: 50px; top: 76px; font-size: 12px; }
  .back__strip {
    position: absolute; left: 0; top: 128px; bottom: 0; width: 26px;
    background: var(--strip);
    display: flex; flex-direction: column; align-items: center;
    padding-top: 10px; gap: 9px;
  }
  .back__strip svg { width: 12px; height: 12px; fill: none; stroke: #fff; stroke-width: 1.6; }
  .contact {
    position: absolute; left: 44px; top: 140px;
    list-style: none; font-size: 13px; line-height: 17px;
  }
  .contact .gap { margin-top: 2px; }
</style>
</head>
<body>
<main class="canvas">

  <section class="card front" aria-label="Card front">
    <div class="brand"><span class="brand__dot"></span>Alder Financial</div>
    <div class="front__band"></div>
    <p class="front__title">YOUR NAME &nbsp;/ <span class="role">designation</span></p>
  </section>

  <section class="card back" aria-label="Card back">
    <div class="back__brandzone">
      <div class="brand"><span class="brand__dot"></span>Alder Financial</div>
    </div>
    <div class="back__panel">
      <p class="back__name">your name</p>
      <p class="back__role">designation</p>
      <div class="back__strip" aria-hidden="true">
        <svg viewBox="0 0 12 12"><path d="M6 11 C3 7 2.5 5.5 2.5 4.5 A3.5 3.5 0 0 1 9.5 4.5 C9.5 5.5 9 7 6 11Z"/><circle cx="6" cy="4.5" r="1.1"/></svg>
        <svg viewBox="0 0 12 12" style="margin-top:10px"><rect x="3.5" y="1" width="5" height="10" rx="1"/></svg>
        <svg viewBox="0 0 12 12"><rect x="3.5" y="1" width="5" height="10" rx="1"/></svg>
        <svg viewBox="0 0 12 12"><rect x="1" y="2.5" width="10" height="7"/><path d="M1 2.5 L6 6.5 L11 2.5"/></svg>
        <svg viewBox="0 0 12 12"><circle cx="6" cy="6" r="4.8"/><path d="M1.2 6 H10.8 M6 1.2 C3.8 4 3.8 8 6 10.8 M6 1.2 C8.2 4 8.2 8 6 10.8"/></svg>
      </div>
      <ul class="contact">
        <li>address (street address</li>
        <li>suite number, city, state, zip</li>
        <li class="gap">0123 456 789</li>
        <li>0123 456 789</li>
        <li class="gap">youremail@mail.com</li>
        <li>www.yourwebsite.com</li>
      </ul>
    </div>
  </section>

</main>
</body>
</html>
```